Young, dynamic furniture company needs a new business card design

We require a new business card design for our modern furniture company which supplies furniture and appliances to the property and development market.
Oakridge Interiors has become one of the leading furniture & appliance suppliers to the property market withing London. With over 10 years experience, we have increased our business to supply not only private landlords and managing agents, but also property developers, housing associations and local councils.
We offer not only a complete range of furniture which includes beds, wardrobes, dining sets and sofas, but also a high quality, full delivery and assembly service to help you with all our furnishing needs.

Target Market(s)

Private landlords, estate agents, letting agents, property management companies

Industry/Entity Type

Business

Contact Information for Business Card

Name,
Title,
Address,
Mobile,
Telephone,
Fax, Website, email address

Font styles to use
Sans Serif

Colors
3176b5
0555a3
85abd2
cfdeed

Requirements
Must have
• All the above information for each of our staff, along with our logo

```html
<!DOCTYPE html>
<html lang="en">
<head>
<meta charset="utf-8">
<title>Oakridge Interiors — Business Card</title>
<link rel="stylesheet" href="https://fonts.googleapis.com/css2?family=Roboto:wght@300;400;700;900&display=swap">
<style>
  :root {
    --bg: #1c1c1e;
    --white: #ffffff;
    --ink: #2b2b2e;
    --ink-soft: #555558;
    --blue-deep: #1d3f86;
    --blue-main: #0555a3;
    --blue-mid: #3176b5;
    --blue-light: #85abd2;
    --blue-pale: #cfdeed;
    --ring: #8a8a8e;
  }
  * { box-sizing: border-box; margin: 0; padding: 0; }
  html, body {
    width: 1200px; height: 923px; overflow: hidden;
    background: var(--bg);
    font-family: "Roboto", sans-serif;
  }
  .canvas { position: relative; width: 1200px; height: 923px; }

  .card {
    position: absolute;
    width: 560px; height: 320px;
    border-radius: 22px;
    overflow: hidden;
    background: var(--white);
  }
  .card--back { left: 570px; top: 120px; }
  .card--front { left: 70px; top: 480px; }

  /* Back side */
  .back-brand {
    position: absolute; inset: 0;
    display: flex; flex-direction: column; align-items: center; justify-content: center;
    text-align: center; color: var(--ink);
  }
  .brand-name { font-weight: 400; font-size: 30px; letter-spacing: 0.5px; }
  .brand-tagline { font-weight: 300; font-size: 12px; letter-spacing: 1.2px; color: var(--ink-soft); margin-top: 4px; }
  .back-web { font-weight: 700; font-size: 15px; margin-top: 42px; color: var(--ink); }

  /* Front side */
  .front-art { position: absolute; inset: 0; }
  .front-brand { position: absolute; left: 40px; top: 56px; color: var(--ink); }
  .front-brand .brand-name { font-size: 26px; }
  .front-brand .brand-tagline { font-size: 10px; }

  .contact {
    position: absolute; right: 28px; top: 132px;
    text-align: right; color: var(--white);
    font-size: 13px; line-height: 18px;
  }
  .contact__name { font-weight: 900; font-size: 17px; line-height: 20px; }
  .contact__title { font-weight: 400; margin-bottom: 6px; }
  .contact__address { margin-bottom: 6px; }
  .contact__line { display: flex; justify-content: flex-end; align-items: center; gap: 8px; }
  .contact__line svg { width: 13px; height: 13px; flex: none; }
</style>
</head>
<body>
<div class="canvas">

  <section class="card card--back" aria-label="Card back">
    <div class="back-brand">
      <div class="brand-name">Oakridge Interiors</div>
      <div class="brand-tagline">TRADE FURNITURE SOLUTIONS</div>
      <div class="back-web">www.oakridgeinteriors.com</div>
    </div>
  </section>

  <section class="card card--front" aria-label="Card front">
    <svg class="front-art" viewBox="0 0 560 320" width="560" height="320" aria-hidden="true">
      <defs>
        <linearGradient id="frontBlue" x1="0" y1="1" x2="1" y2="0">
          <stop offset="0" stop-color="#1d3f86"/>
          <stop offset="0.55" stop-color="#1f4f96"/>
          <stop offset="1" stop-color="#0555a3"/>
        </linearGradient>
        <linearGradient id="ringGrey" x1="0" y1="0" x2="1" y2="0">
          <stop offset="0" stop-color="#cfcfd2"/>
          <stop offset="0.6" stop-color="#6d6d72"/>
          <stop offset="1" stop-color="#b8b8bc"/>
        </linearGradient>
      </defs>
      <rect class="front-band" width="560" height="320" fill="url(#frontBlue)"/>
      <circle class="front-ring" cx="230" cy="-110" r="309" fill="url(#ringGrey)"/>
      <circle class="front-ring-gap" cx="230" cy="-110" r="304" fill="#ffffff"/>
      <circle class="front-ring-inner" cx="230" cy="-110" r="302" fill="#3a3a3e"/>
      <circle class="front-panel" cx="230" cy="-110" r="300" fill="#ffffff"/>
    </svg>

    <div class="front-brand">
      <div class="brand-name">Oakridge Interiors</div>
      <div class="brand-tagline">TRADE FURNITURE SOLUTIONS</div>
    </div>

    <div class="contact">
      <div class="contact__name">Daniel Reeves</div>
      <div class="contact__title">Job Title</div>
      <div class="contact__address">34 Street Name<br>City Name, Country 4567</div>
      <div class="contact__line">000 1234 5678
        <svg viewBox="0 0 16 16" aria-label="Telephone"><path fill="#fff" d="M2 5c0-2 3-3 6-3s6 1 6 3v1h-3V5H5v1H2zM4 7h8l2 6H2z"/></svg>
      </div>
      <div class="contact__line">000 1234 5678
        <svg viewBox="0 0 16 16" aria-label="Mobile"><rect x="4.5" y="1" width="7" height="14" rx="1.5" fill="none" stroke="#fff" stroke-width="1.6"/><circle cx="8" cy="12.5" r="0.9" fill="#fff"/></svg>
      </div>
      <div class="contact__line">000 1234 5678
        <svg viewBox="0 0 16 16" aria-label="Fax"><rect x="4" y="1" width="8" height="5" fill="#fff"/><rect x="1" y="6" width="14" height="6" rx="1" fill="#fff"/><rect x="4" y="10" width="8" height="5" fill="#fff" stroke="#1d3f86" stroke-width="1"/></svg>
      </div>
      <div class="contact__line">info@oakridgeinteriors.com
        <svg viewBox="0 0 16 16" aria-label="Email"><rect x="1" y="3" width="14" height="10" fill="#fff"/><path d="M1 3l7 6 7-6" fill="none" stroke="#1d3f86" stroke-width="1.2"/></svg>
      </div>
      <div class="contact__line">www.oakridgeinteriors.com
        <svg viewBox="0 0 16 16" aria-label="Website"><circle cx="8" cy="8" r="6.5" fill="none" stroke="#fff" stroke-width="1.3"/><ellipse cx="8" cy="8" rx="3" ry="6.5" fill="none" stroke="#fff" stroke-width="1"/><path d="M1.5 8h13M2.5 5h11M2.5 11h11" stroke="#fff" stroke-width="1"/></svg>
      </div>
    </div>
  </section>

</div>
</body>
</html>
```